VENTURE CAPITAL GROUP BUSINESS CARD DESIGN

Venture Capital Group based in SF looking for a bold business card design. No trendy colour explosion, 3D effects etc. Just "simple" optical effects. Works on your brain, keeps your eye focused and sticks to your mind.
Target Market(s)
Technology startups
Industry/Entity Type
Venture Capital
Contact Information for Business Card
DESMOND WHITLAKE
MANAGING PARTNER
187 FENWORTH ST SAN FRANCISCO, CA 94187
415.555.0142 O
415.555.0147 F
415.555.0193 C
desmond@veldtmoorcapital.ventures

```html
<!DOCTYPE html>
<html lang="en">
<head>
<meta charset="utf-8">
<title>Veldtmoor Capital Group – Business Card</title>
<link href="https://fonts.googleapis.com/css2?family=Cardo:wght@400;700&display=swap" rel="stylesheet">
<style>
  :root {
    --backdrop: #1c1c1c;
    --card-dark: #222623;
    --card-dark-edge: #2c302d;
    --paper: #f4f4f4;
    --green: #1f8a3a;
    --green-deep: #18702e;
    --green-text: #1d7a35;
    --ink: #2a2a2a;
    --band-text: #eaf4ec;
    --rule: #b9b9b9;
  }
  * { box-sizing: border-box; margin: 0; padding: 0; }
  html, body { width: 1200px; height: 873px; overflow: hidden; }
  body {
    background: var(--backdrop);
    font-family: "Cardo", Georgia, serif;
    position: relative;
  }

  .card {
    position: absolute;
    width: 580px;
    height: 331px;
    border-radius: 3px;
    box-shadow: 0 14px 40px rgba(0,0,0,.55);
    overflow: hidden;
  }

  /* Back side */
  .card-back {
    left: 90px; top: 90px;
    background: radial-gradient(ellipse at 50% 45%, var(--card-dark-edge), var(--card-dark) 70%);
    display: flex; align-items: center; justify-content: center;
  }
  .card-back .wordmark {
    font-size: 40px;
    font-weight: 400;
    color: var(--green);
    letter-spacing: 1px;
    text-align: center;
  }

  /* Front side */
  .card-front {
    left: 530px; top: 452px;
    background: var(--paper);
  }
  .front-top { position: absolute; left: 0; top: 0; width: 100%; height: 212px; }
  .front-wordmark {
    position: absolute; top: 46px; width: 100%;
    text-align: center;
    font-size: 27px; color: var(--green-text);
  }
  .identity {
    position: absolute; right: 318px; top: 140px;
    text-align: right;
  }
  .identity .person { font-size: 19px; font-weight: 700; color: var(--green-text); }
  .identity .role { font-size: 14px; color: var(--ink); margin-top: 2px; }
  .divider {
    position: absolute; left: 282px; top: 110px;
    width: 2px; height: 80px;
    background: linear-gradient(to bottom, transparent, var(--rule), transparent);
  }
  .contact-list {
    position: absolute; left: 302px; top: 108px;
    list-style: none;
    font-size: 14.5px; color: var(--ink);
  }
  .contact-list li { display: flex; align-items: center; gap: 8px; height: 24px; }
  .contact-list svg { width: 13px; height: 13px; fill: var(--green); flex: none; }

  .band {
    position: absolute; left: 0; bottom: 0;
    width: 100%; height: 119px;
    background: linear-gradient(to bottom, var(--green), var(--green-deep));
    color: var(--band-text);
    text-align: center;
  }
  .band-title {
    display: flex; align-items: center; justify-content: center; gap: 12px;
    margin-top: 14px;
    font-size: 17px; font-weight: 700; letter-spacing: 1px;
  }
  .band-title::before, .band-title::after {
    content: ""; width: 70px; height: 1px; background: var(--band-text);
  }
  .band-details {
    display: flex; justify-content: center; gap: 20px;
    margin-top: 12px; font-size: 15px;
  }
  .band-details span { display: inline-flex; align-items: center; gap: 6px; }
  .band-details svg { width: 14px; height: 14px; fill: var(--band-text); }
  .band-web { margin-top: 9px; font-size: 15px; letter-spacing: 1px; }
</style>
</head>
<body>

  <section class="card card-back" aria-label="Card back">
    <div class="wordmark">Veldtmoor Capital Group</div>
  </section>

  <section class="card card-front" aria-label="Card front">
    <div class="front-top">
      <div class="front-wordmark">Veldtmoor Capital Group</div>

      <div class="identity">
        <div class="person">Desmond Whitlake</div>
        <div class="role">Managing Partner</div>
      </div>

      <div class="divider"></div>

      <ul class="contact-list">
        <li>
          <svg viewBox="0 0 24 24" aria-hidden="true"><path d="M6.6 10.8a15 15 0 0 0 6.6 6.6l2.2-2.2a1 1 0 0 1 1-.25 11.4 11.4 0 0 0 3.6.57 1 1 0 0 1 1 1V20a1 1 0 0 1-1 1A17 17 0 0 1 3 4a1 1 0 0 1 1-1h3.5a1 1 0 0 1 1 1c0 1.25.2 2.45.57 3.6a1 1 0 0 1-.25 1z"/></svg>
          415.555.0147
        </li>
        <li>
          <svg viewBox="0 0 24 24" aria-hidden="true"><path d="M6 2h12v6H6zM3 9h18a1 1 0 0 1 1 1v7h-4v5H6v-5H2v-7a1 1 0 0 1 1-1zm5 7v4h8v-4z"/></svg>
          415.555.0193
        </li>
        <li>
          <svg viewBox="0 0 24 24" aria-hidden="true"><path d="M2 5h20v14H2zm2 2v.5l8 5.5 8-5.5V7zm0 3v7h16v-7l-8 5.5z"/></svg>
          desmond@veldtmoorcapital.ventures
        </li>
      </ul>
    </div>

    <div class="band">
      <div class="band-title">VELDTMOOR CAPITAL GROUP</div>
      <div class="band-details">
        <span>
          <svg viewBox="0 0 24 24" aria-hidden="true"><path d="M6.6 10.8a15 15 0 0 0 6.6 6.6l2.2-2.2a1 1 0 0 1 1-.25 11.4 11.4 0 0 0 3.6.57 1 1 0 0 1 1 1V20a1 1 0 0 1-1 1A17 17 0 0 1 3 4a1 1 0 0 1 1-1h3.5a1 1 0 0 1 1 1c0 1.25.2 2.45.57 3.6a1 1 0 0 1-.25 1z"/></svg>
          415.555.0142
        </span>
        <span>
          <svg viewBox="0 0 24 24" aria-hidden="true"><path d="M12 2a7 7 0 0 0-7 7c0 5 7 13 7 13s7-8 7-13a7 7 0 0 0-7-7zm0 9.5A2.5 2.5 0 1 1 12 6.5a2.5 2.5 0 0 1 0 5z"/></svg>
          187 Fenworth St San Francisco, CA 94187
        </span>
      </div>
      <div class="band-web">www.veldtmoorcapital.ventures</div>
    </div>
  </section>

</body>
</html>
```